New Innovative Counselling and psychotherapy Service needs Business Card design

Keep it simple and professional. On one side, just company name and logo (perhaps in all blue) and maybe a tag line.

On other side (all white) my name and Qualifications in centre

Industry/Entity Type

Health And Wellness

Contact Information for Business Card

Dara Whelby
Counsellor & Psychotherapist
BSc (Psychol.), BA, Dip. (Couns. & Psych.), PG.Cert (CBT), FGTrK, ONRE

I will also require Mobile no, Email and web site address of which I'll pass on to final designer.

Font styles to use
Sans Serif

Requirements
Must have
• My Logo Only and please use the colours in logo that is in it.
Should not have
• Any other images

```html
<!DOCTYPE html>
<html lang="en">
<head>
<meta charset="utf-8">
<title>Brightwell Lane – Business Card</title>
<link rel="stylesheet" href="https://fonts.googleapis.com/css2?family=Lato:ital,wght@0,400;0,700;1,400&display=swap">
<style>
  :root {
    --stage: #1b1b1b;
    --card-light: #f3f3f3;
    --brand-blue: #46b3ec;
    --brand-green: #8fd05a;
    --ink: #2a2a2a;
    --ink-soft: #3a3a3a;
    --white: #ffffff;
  }
  * { margin: 0; padding: 0; box-sizing: border-box; }
  html, body { width: 1200px; height: 900px; overflow: hidden; }
  body {
    background: var(--stage);
    font-family: "Lato", sans-serif;
    position: relative;
  }
  .card {
    position: absolute;
    top: 200px;
    width: 310px;
    height: 502px;
  }
  .card--front {
    left: 253px;
    background: var(--card-light);
    border-radius: 60px 0 60px 0;
  }
  .card--back {
    left: 627px;
    background: var(--brand-blue);
    border-radius: 0 60px 0 60px;
  }
  .brand {
    position: absolute;
    left: 29px;
    top: 130px;
    display: flex;
    align-items: center;
    gap: 17px;
  }
  .brand__dot {
    width: 50px; height: 50px;
    border-radius: 50%;
    background: var(--brand-blue);
  }
  .brand__name {
    font-size: 23px;
    font-weight: 400;
    color: var(--ink);
    letter-spacing: 0.2px;
  }
  .person {
    position: absolute;
    left: 33px;
    top: 308px;
    color: var(--ink-soft);
  }
  .person__name {
    font-size: 19px;
    font-weight: 400;
    line-height: 22px;
    letter-spacing: 0.3px;
  }
  .person__first { color: var(--brand-blue); }
  .person__last { color: var(--brand-green); }
  .person__role {
    font-size: 14px;
    line-height: 18px;
  }
  .person__quals {
    margin-top: 3px;
    font-size: 14px;
    font-style: italic;
    line-height: 19px;
  }
  .contact {
    list-style: none;
    margin-top: 19px;
    font-size: 14.5px;
    line-height: 18.5px;
  }
  .contact li { display: flex; align-items: center; gap: 3px; }
  .contact svg { width: 12px; height: 12px; fill: var(--brand-blue); }
  .back__mark {
    position: absolute;
    left: 60px;
    top: 153px;
    width: 190px;
    height: 190px;
    border-radius: 50%;
    background: var(--white);
  }
  .tagline {
    position: absolute;
    left: 0; right: 0;
    top: 417px;
    text-align: center;
    color: var(--white);
    font-size: 14px;
    font-weight: 700;
    letter-spacing: 1px;
    line-height: 22px;
  }
</style>
</head>
<body>
  <section class="card card--front">
    <div class="brand">
      <span class="brand__dot"></span>
      <span class="brand__name">Brightwell Lane</span>
    </div>
    <div class="person">
      <h1 class="person__name"><span class="person__first">DARA</span> <span class="person__last">WHELBY</span></h1>
      <p class="person__role">Counsellor &amp; Psychotherapist</p>
      <p class="person__quals">BSc (Psychol.), BA,Dip. (Couns. &amp; Psych.),<br>PG.Cert (CBT), FGTrK, ONRE</p>
      <ul class="contact">
        <li><svg viewBox="0 0 12 12" aria-hidden="true"><path d="M1 4c0-2 2-3 5-3s5 1 5 3l-2 1-1-2H4L3 5zM2 6h8v5H2z"/></svg>086 5550 127</li>
        <li><svg viewBox="0 0 12 12" aria-hidden="true"><path d="M1 3h10v7H1zM1.8 3.6 6 7l4.2-3.4v-.2H1.8z" fill-rule="evenodd"/></svg>info@brightwelllane.com</li>
        <li><svg viewBox="0 0 12 12" aria-hidden="true"><circle cx="6" cy="6.5" r="5"/></svg>www.brightwelllane.com</li>
      </ul>
    </div>
  </section>

  <section class="card card--back">
    <span class="back__mark" aria-hidden="true"></span>
    <p class="tagline">CARING FOR YOUR&nbsp; PSYCHOLOGICAL<br>WELL-BEING IS OUR TOP PRIORITY</p>
  </section>
</body>
</html>
```